Email Signature Design

Please design an email signature, the below is an example of our current design;
___

HARCOURT ESTATE PARTNERS PTY LTD
DOMINIC FARRADAY
Licensed Strata and Community Manager

148 Calloway Street,
BRAMWELL NSW 2164

P: 02.9374.6082 F: 9463.7820
Website: www.harcourtestate.com.au

This e-mail message and accompanying data may contain information that is confidential and private. If you are not the intended recipient, the use, dissemination, distribution or copying of this message or data is prohibited.

If you have received this e-mail in error please notify us immediately and delete all material pertaining to this e-mail. strata@harcourtestate.com.au

___

We would like to incorporate our logo and company colours, you can view the colours and feel of image at www.harcourtestate.com.au

Industry/Entity Type

It Company

Requirements
Must have
• use of logo and company colours (image)

```html
<!DOCTYPE html>
<html lang="en">
<head>
<meta charset="utf-8">
<title>Harcourt Estate Partners – Email Signature</title>
<link rel="stylesheet" href="https://fonts.googleapis.com/css2?family=Source+Sans+3:wght@400;600;700&display=swap">
<style>
  :root {
    --olive: #7f7d3e;
    --slate: #6d6e71;
    --ink: #4a4a4c;
    --rule: #dcdcdc;
    --paper: #ffffff;
    --backdrop: #ecebe6;
  }
  * { box-sizing: border-box; margin: 0; padding: 0; }
  html, body {
    width: 1200px; height: 440px; overflow: hidden;
    background: var(--backdrop);
    font-family: "Source Sans 3", Arial, sans-serif;
  }
  .signature {
    position: absolute; left: 35px; top: 32px;
    width: 1130px; height: 376px;
    background: var(--paper);
    border: 1px solid #cfcfcf;
    overflow: hidden;
  }
  .brand-square {
    position: absolute; left: 150px; top: 70px;
    width: 150px; height: 150px;
    background: var(--olive);
  }
  .brand-name {
    position: absolute; left: 112px; top: 244px;
    font-size: 33px; font-weight: 700; line-height: 1;
    letter-spacing: 0.6px;
    color: var(--olive);
    white-space: nowrap;
  }
  .divider {
    position: absolute; left: 597px; top: 47px;
    width: 1px; height: 281px;
    background: var(--rule);
  }
  .line {
    position: absolute; left: 628px;
    white-space: nowrap; line-height: 1;
  }
  .person-name { top: 46px; font-size: 26px; font-weight: 700; color: var(--olive); }
  .person-role { top: 81px; font-size: 24px; color: var(--slate); }
  .company-name { top: 129px; font-size: 23.5px; color: var(--olive); }
  .company-address { top: 158px; font-size: 24px; color: var(--ink); }
  .contact {
    display: flex; align-items: center;
    font-size: 24px; color: var(--ink);
  }
  .contact-phone { top: 206px; }
  .contact-fax { top: 235px; }
  .contact-email { top: 264px; }
  .contact-web { top: 294px; }
  .contact-icon {
    width: 18px; height: 18px; margin-right: 13px; flex: none;
  }
  .contact-icon .solid { fill: var(--olive); stroke: none; }
  .contact-icon .outline { fill: none; stroke: var(--olive); }
  .contact-icon .knockout { fill: none; stroke: #fff; }
  .contact-icon .cut { fill: #fff; stroke: none; }
  .footer-band {
    position: absolute; left: 0; bottom: 0;
    width: 1130px; height: 24px;
  }
  .band-olive { fill: var(--olive); }
  .band-slate { fill: var(--slate); }
</style>
</head>
<body>
  <div class="signature">
    <div class="brand-square"></div>
    <div class="brand-name">HARCOURT ESTATE PARTNERS</div>

    <div class="divider"></div>

    <div class="line person-name">DOMINIC FARRADAY</div>
    <div class="line person-role">Licensed Strata and Community Manager</div>
    <div class="line company-name">HARCOURT ESTATE PARTNERS PTY LTD</div>
    <div class="line company-address">148 Calloway Street, BRAMWELL NSW 2164</div>

    <div class="line contact contact-phone">
      <svg class="contact-icon" viewBox="0 0 20 20" aria-hidden="true">
        <circle class="outline" cx="10" cy="10" r="8.5" stroke-width="1.4"/>
        <path class="solid" d="M7 5.5c-1 1-1 3 .5 5.5s3.5 4 5 4l1-1.3-1.8-1.6-1 .8c-.8-.4-2-1.8-2.4-2.8l.9-.9L8.2 5z"/>
      </svg>
      02.9374.6082
    </div>
    <div class="line contact contact-fax">
      <svg class="contact-icon" viewBox="0 0 20 20" aria-hidden="true">
        <rect class="solid" x="5" y="2" width="10" height="6"/>
        <rect class="solid" x="1" y="8" width="18" height="9" rx="1.5"/>
        <rect class="cut" x="5" y="11" width="10" height="2"/>
      </svg>
      9463.7820
    </div>
    <div class="line contact contact-email">
      <svg class="contact-icon" viewBox="0 0 20 20" aria-hidden="true">
        <rect class="solid" x="1" y="5" width="18" height="12"/>
        <path class="knockout" d="M1.5 5.5 10 12l8.5-6.5" stroke-width="1.4"/>
      </svg>
      strata@harcourtestate.com.au
    </div>
    <div class="line contact contact-web">
      <svg class="contact-icon" viewBox="0 0 20 20" aria-hidden="true">
        <circle class="outline" cx="10" cy="10" r="8.5" stroke-width="1.5"/>
        <ellipse class="outline" cx="10" cy="10" rx="3.8" ry="8.5" stroke-width="1.2"/>
        <path class="outline" d="M1.5 10h17M3 5.5h14M3 14.5h14" stroke-width="1.2"/>
      </svg>
      www.harcourtestate.com.au
    </div>

    <svg class="footer-band" viewBox="0 0 1130 24" preserveAspectRatio="none" aria-hidden="true">
      <polygon class="band-olive" points="0,0 591,0 536,24 0,24"/>
      <polygon class="band-slate" points="616,0 1130,0 1130,24 561,24"/>
    </svg>
  </div>
</body>
</html>
```